Fun Employee News and Engagement Portal - Tidy Hearth Company

We are looking for a clean, but fun WordPress template for an internal employee engagement website. The site will be a place we share news, fun stories and pictures. We'll provide space for our employees to post comments, etc.
We are a deep dish pizza restaurant with a rich history. I'd love to see your take on a look and feel for us! The site will be called Bim-Zee. I've posted some images and colors along with this brief description.
Focus on making the template whimsical and fun! (Extra point for focusing on the "Lettering in lights" ).
I will continue to post additional pieces of art and content examples.
Reason: Our team is continuing to review designs. We've decided to extend the timing a few more days. Good luck! Make it playful!
Reason: We need more time with our team to review these designs. We are going to extend one more time!
Reason: Still trying to get enough time to review with the Bim-Zee team!
Reason: We are continuing to evaluate designs. Thank you!
Industry/Entity Type
American Restaurant
Number of Pages Required
1 page
Look and feel
Each slider illustrates characteristics of the customer's brand and the style your logo design should communicate.

```html
<!DOCTYPE html>
<html lang="en">
<head>
<meta charset="utf-8">
<title>Bim-Zee — Employee news &amp; fun facts</title>
<link rel="stylesheet" href="https://fonts.googleapis.com/css2?family=Bitter:wght@500;700&family=Jost:wght@400;500;600&family=Open+Sans:wght@400;600;700&display=swap">
<style>
:root{
  --red:#e2322f;
  --ink:#2b2b2b;
  --muted:#8a8a8a;
  --line:#e6e6e6;
  --soft:#f3f3f3;
  --panel-head:#f4f5f6;
  --star:#f0a81c;
  --night:#1e2029;
  --footer:#262626;
  --white:#ffffff;
}
*{box-sizing:border-box;margin:0;padding:0}
html,body{width:1200px;height:2278px;overflow:hidden;background:var(--white)}
body{position:relative;font-family:"Open Sans",Arial,sans-serif;color:var(--ink)}
.abs{position:absolute}

/* header */
.top-rule{left:0;top:0;width:1200px;height:4px;background:var(--red)}
.site-header{left:0;top:4px;width:1200px;height:114px;background:var(--white)}
.brand{left:97px;top:42px;display:flex;align-items:center;gap:10px}
.brand-dot{width:38px;height:38px;border-radius:50%;background:var(--red)}
.brand-name{font-family:"Jost",sans-serif;font-weight:600;font-size:33px;color:#111;letter-spacing:.5px}
.contact-bar{right:90px;top:22px;display:flex;align-items:center;gap:8px;font-size:19px;color:#222}
.contact-bar svg{display:block}
.socials{display:flex;gap:6px;margin-left:14px}
.socials span{width:18px;height:18px;border-radius:3px;display:block}
.nav{left:443px;top:62px;display:flex;align-items:center;font-size:16px;color:#222}
.nav a{color:inherit;text-decoration:none;display:block}
.nav .is-active{border:1.5px solid var(--red);color:var(--red);border-radius:16px;width:95px;height:29px;line-height:26px;text-align:center}
.nav .item-about{margin-left:24px}
.nav .item-menus{margin-left:46px}
.nav .item-products{margin-left:46px}
.nav .item-blog{margin-left:50px}
.nav .item-contact{margin-left:47px}

/* hero */
.hero{left:0;top:118px;width:1200px;height:573px;overflow:hidden;
  background:radial-gradient(ellipse 290px 260px at 768px 255px,#d9682e 0%,#c4552a 55%,rgba(40,30,34,0) 100%),
  linear-gradient(180deg,#232533 0%,#1b1c25 100%)}
.hero-title{left:90px;top:218px;font-family:"Jost",sans-serif;font-weight:500;font-size:56px;color:var(--white);letter-spacing:1px;line-height:1}
.hero-sub{left:90px;top:278px;font-family:"Jost",sans-serif;font-size:29px;color:var(--white)}
.hero-arrow{top:491px;width:30px;height:30px;border-radius:50%;background:#111;border:1.5px solid #555}
.hero-arrow svg{display:block;margin:8px auto}
.hero-wave{left:0;top:608px;width:1200px;height:84px}

/* welcome */
.section-title{width:1200px;left:0;text-align:center;font-family:"Bitter",serif;font-weight:700;font-size:24px;letter-spacing:1px;color:#2a2a2a}
.welcome-text{left:129px;top:786px;width:942px;text-align:center;font-size:14px;line-height:21px;color:var(--muted)}

/* proposals */
.proposals{left:0;top:904px;width:1200px;height:405px;background:var(--soft)}
.card{top:1007px;width:322px;height:258px;background:var(--white);box-shadow:0 1px 4px rgba(0,0,0,.12)}
.card-media{height:167px}
.card-title{margin-top:21px;text-align:center;font-family:"Bitter",serif;font-weight:500;font-size:12.5px;letter-spacing:.5px;color:#333}
.card-text{margin:8px auto 0;width:260px;text-align:center;font-size:10.5px;line-height:14px;color:var(--muted)}
.slide-arrow{top:1130px}

/* panels */
.panel{background:var(--white);box-shadow:0 1px 5px rgba(0,0,0,.14)}
.panel-head{height:40px;line-height:40px;padding-left:17px;background:var(--panel-head);border-bottom:1px solid var(--line);font-family:"Bitter",serif;font-weight:500;font-size:14px;letter-spacing:.5px;color:#444}
.story{display:flex;align-items:center;height:84px;padding-left:10px;border-bottom:1px solid var(--line)}
.story-thumb{width:58px;height:55px;border-radius:3px;flex:none}
.story-body{margin-left:13px}
.story-name{font-size:13px;color:#333}
.stars{display:flex;gap:2px;margin:3px 0 3px}
.stars i{width:9px;height:9px;display:block;clip-path:polygon(50% 0,61% 35%,98% 35%,68% 57%,79% 91%,50% 70%,21% 91%,32% 57%,2% 35%,39% 35%);background:var(--star)}
.stars i.off{background:#cfcfcf}
.story-meta{font-size:10.5px;color:#666}
.view-more{text-align:center;font-size:12px;color:var(--red);padding-top:16px}

.post{left:360px;top:1384px;width:485px;height:466px}
.avatar{border-radius:50%;background:linear-gradient(135deg,#c79b7a,#6e5040)}
.post-author{left:52px;top:20px;font-family:"Bitter",serif;font-weight:700;font-size:15px;font-variant:small-caps;letter-spacing:.5px;color:#333}
.post-stats{left:80px;top:49px;font-size:11px;color:#444}
.post-media{left:26px;top:79px;width:434px;height:170px}
.post-caption{left:26px;top:268px;font-family:"Bitter",serif;font-weight:700;font-size:13px;font-variant:small-caps;letter-spacing:.5px;color:#333}
.post-text{left:26px;top:296px;width:434px;font-size:11.5px;line-height:19px;color:#555}
.post-rule{left:26px;top:352px;width:434px;height:1px;background:var(--line)}
.post-actions{left:26px;top:372px;display:flex;align-items:center;font-size:10.5px;color:#444}
.post-actions span{display:flex;align-items:center;gap:6px}
.post-actions .sep{width:1px;height:14px;background:#ccc;margin:0 14px}
.comment-box{left:77px;top:405px;width:383px;height:35px;border:1px solid #dcdcdc;border-radius:3px;font-size:11px;color:#444;padding:9px 0 0 13px}

/* partners */
.partner{top:1982px;height:60px}

/* footer */
.site-footer{left:0;top:2096px;width:1200px;height:182px;background:var(--footer);color:var(--white)}
.footer-links{left:0;top:48px;width:1200px;text-align:center;font-size:12px;letter-spacing:.3px}
.footer-links span{margin:0 10px}
.footer-social{left:0;top:82px;width:1200px;display:flex;justify-content:center;gap:9px}
.footer-social i{width:28px;height:28px;border-radius:50%;border:1.5px solid #cfcfcf;display:block}
.copyright{left:0;top:124px;width:1200px;text-align:center;font-size:12px}
</style>
</head>
<body>

<div class="abs top-rule"></div>
<header class="abs site-header">
  <div class="abs brand"><span class="brand-dot"></span><span class="brand-name">BIM-ZEE</span></div>
  <div class="abs contact-bar">
    <svg width="17" height="17" viewBox="0 0 17 17"><rect width="17" height="17" rx="3" fill="var(--red)"/><path d="M5 4l2 0 1 3-1.3 1a6 6 0 0 0 2.3 2.3l1-1.3 3 1v2c0 .6-.5 1-1 1A8 8 0 0 1 4 5c0-.5.4-1 1-1z" fill="#fff"/></svg>
    <span>555 214 0188</span>
    <span class="socials">
      <span style="background:#3b5ca0"></span>
      <span style="background:#2aa3ef"></span>
      <span style="background:#1a7bb9"></span>
      <span style="background:#e04a39"></span>
    </span>
  </div>
  <nav class="abs nav">
    <a class="is-active">HOME</a>
    <a class="item-about">ABOUT US</a>
    <a class="item-menus">MENUS</a>
    <a class="item-products">PRODUCTS</a>
    <a class="item-blog">BLOG</a>
    <a class="item-contact">CONTACT US</a>
  </nav>
</header>

<section class="abs hero" role="img" aria-label="Sliced pizza with tomatoes, mushrooms, olives and basil on a dark stone surface">
  <div class="abs hero-title">BIM-ZEE</div>
  <div class="abs hero-sub">Employee news &amp; fun facts</div>
  <div class="abs hero-arrow" style="left:87px"><svg width="12" height="12" viewBox="0 0 12 12"><path d="M8 1L3 6l5 5" stroke="#fff" stroke-width="2" fill="none"/></svg></div>
  <div class="abs hero-arrow" style="left:125px"><svg width="12" height="12" viewBox="0 0 12 12"><path d="M4 1l5 5-5 5" stroke="#fff" stroke-width="2" fill="none"/></svg></div>
</section>
<svg class="abs hero-wave" viewBox="0 400 790 56" preserveAspectRatio="none">
  <polygon points="0,432 680,405 790,427 790,456 0,456" fill="var(--red)"/>
  <polygon points="0,456 0,455 265,455 636,426 790,452 790,456" fill="#fff"/>
</svg>

<h1 class="abs section-title" style="top:740px">WELCOME TO&nbsp; BIM-ZEE</h1>
<p class="abs welcome-text">It is a long established fact that a reader will be distracted by the readable content of a page when looking at its layout. The point of using Lorem Ipsum is that it has a more-or-less normal distribution of letters, as opposed to using 'Content here, content here', making it look like readable English. Many desktop publishing packages and web page editors now use Lorem Ipsum as their default model text,</p>

<section class="abs proposals"></section>
<h2 class="abs section-title" style="top:950px">LATEST PROPOSALS</h2>
<svg class="abs slide-arrow" style="left:48px" width="18" height="40" viewBox="0 0 18 40"><path d="M16 2L3 20l13 18" stroke="#bdbdbd" stroke-width="1.5" fill="none"/></svg>
<svg class="abs slide-arrow" style="left:1131px" width="18" height="40" viewBox="0 0 18 40"><path d="M2 2l13 18L2 38" stroke="#bdbdbd" stroke-width="1.5" fill="none"/></svg>

<article class="abs card" style="left:94px">
  <div class="card-media" role="img" aria-label="Heart-shaped pepperoni pizza on a wooden board with tomatoes" style="background:linear-gradient(135deg,#6f5a48,#c9862f 55%,#8a6c52)"></div>
  <h3 class="card-title">NEQUE PORRO QUISQUAM</h3>
  <p class="card-text">It has survived not only five centuries, but also the leap into electronic typesetting, remaining</p>
</article>
<article class="abs card" style="left:444px">
  <div class="card-media" role="img" aria-label="Group of friends laughing while sharing pizza" style="background:linear-gradient(135deg,#c7c2bb,#b28a6d 50%,#7d8a96)"></div>
  <h3 class="card-title">NEQUE PORRO QUISQUAM</h3>
  <p class="card-text">It has survived not only five centuries, but also the leap into electronic typesetting, remaining</p>
</article>
<article class="abs card" style="left:788px">
  <div class="card-media" role="img" aria-label="Hands taking slices from a shared pizza box" style="background:linear-gradient(135deg,#d8b48a,#c98f55 50%,#e3d2bf)"></div>
  <h3 class="card-title">NEQUE PORRO QUISQUAM</h3>
  <p class="card-text">It has survived not only five centuries, but also the leap into electronic typesetting, remaining</p>
</article>

<aside class="abs panel" style="left:91px;top:1381px;width:243px;height:513px">
  <div class="panel-head">FUN STORIES</div>
  <div class="story"><div class="story-thumb" role="img" aria-label="Pizza slice" style="background:linear-gradient(135deg,#a3442a,#d78a44)"></div><div class="story-body"><div class="story-name">NEQUE PORRO</div><div class="stars"><i></i><i></i><i></i><i class="off"></i><i class="off"></i></div><div class="story-meta">200 Reviews , 10 Follower</div></div></div>
  <div class="story"><div class="story-thumb" role="img" aria-label="Person eating pizza" style="background:linear-gradient(135deg,#d9cfc7,#a0523e)"></div><div class="story-body"><div class="story-name">ASIF BON VIVEUR</div><div class="stars"><i></i><i></i><i></i><i class="off"></i><i class="off"></i></div><div class="story-meta">200 Reviews , 10 Follower</div></div></div>
  <div class="story"><div class="story-thumb" role="img" aria-label="Whole pizza" style="background:linear-gradient(135deg,#c98a4a,#e8c07a)"></div><div class="story-body"><div class="story-name">NEQUE PORRO</div><div class="stars"><i></i><i></i><i></i><i class="off"></i><i class="off"></i></div><div class="story-meta">200 Reviews , 10 Follower</div></div></div>
  <div class="story"><div class="story-thumb" role="img" aria-label="Person biting a slice" style="background:linear-gradient(135deg,#2c2a30,#9a5a48)"></div><div class="story-body"><div class="story-name">NEQUE PORRO</div><div class="stars"><i></i><i></i><i></i><i class="off"></i><i class="off"></i></div><div class="story-meta">200 Reviews , 10 Follower</div></div></div>
  <div class="story"><div class="story-thumb" role="img" aria-label="Vegetable pizza" style="background:linear-gradient(135deg,#b8502c,#d9a04c)"></div><div class="story-body"><div class="story-name">ASIF BON VIVEUR</div><div class="stars"><i></i><i></i><i></i><i class="off"></i><i class="off"></i></div><div class="story-meta">200 Reviews , 10 Follower</div></div></div>
  <div class="view-more">View More »</div>
</aside>

<article class="abs panel post">
  <div class="abs avatar" style="left:26px;top:18px;width:40px;height:40px" role="img" aria-label="Author avatar"></div>
  <div class="abs post-author" style="left:80px">Dana Mercer</div>
  <div class="abs post-stats">319 Reviews , 432 Followers</div>
  <div class="abs post-media" role="img" aria-label="Friends laughing together while eating pizza" style="background:linear-gradient(135deg,#d7c6b4,#b07d63 45%,#5e7385)"></div>
  <div class="abs post-caption">13 minutes ago&nbsp; via Crumbly for Mobile</div>
  <p class="abs post-text">Lorem ipsum dolor sit amet, consectetur adipiscing elit, sed do eiusmod tempor incididunt ut labore et dolore magna aliqua. Ut enim ad minim</p>
  <div class="abs post-rule"></div>
  <div class="abs post-actions">
    <span><svg width="11" height="11" viewBox="0 0 11 11"><path d="M1 5h2v5H1zM4 5l2-4c1 0 1.5.6 1.3 1.6L7 4h3l-1 6H4z" fill="none" stroke="#666" stroke-width="1"/></svg>LIKE</span>
    <span class="sep"></span>
    <span><svg width="11" height="11" viewBox="0 0 11 11"><path d="M1 2h9v5H4l-3 3z" fill="#666"/></svg>COMMENT</span>
    <span class="sep"></span>
    <span><svg width="11" height="11" viewBox="0 0 11 11"><path d="M6 1l4 4-4 4V7C3 7 2 8 1 10c0-4 2-6 5-6z" fill="#666"/></svg>SHARE</span>
  </div>
  <div class="abs avatar" style="left:26px;top:400px;width:42px;height:42px" role="img" aria-label="Commenter avatar"></div>
  <div class="abs comment-box">write a comment</div>
</article>

<aside class="abs panel" style="left:866px;top:1378px;width:244px;height:516px">
  <div class="panel-head">EMPLOYEE NEW</div>
  <div class="story"><div class="story-thumb" role="img" aria-label="Pizza" style="background:linear-gradient(135deg,#c46a34,#e6b067)"></div><div class="story-body"><div class="story-name">DOLOREM IPSUM</div><div class="stars"><i></i><i></i><i></i><i class="off"></i><i class="off"></i></div><div class="story-meta">200 Reviews , 10 Follower</div></div></div>
  <div class="story"><div class="story-thumb" role="img" aria-label="Pizza slices" style="background:linear-gradient(135deg,#b3552f,#e0b27e)"></div><div class="story-body"><div class="story-name">PORRO QUISQUAM</div><div class="stars"><i></i><i></i><i></i><i class="off"></i><i class="off"></i></div><div class="story-meta">200 Reviews , 10 Follower</div></div></div>
  <div class="story"><div class="story-thumb" role="img" aria-label="Person eating pizza" style="background:linear-gradient(135deg,#d8d0c8,#8a5a44)"></div><div class="story-body"><div class="story-name">DOLOREM IPSUM</div><div class="stars"><i></i><i></i><i></i><i class="off"></i><i class="off"></i></div><div class="story-meta">200 Reviews , 10 Follower</div></div></div>
  <div class="story"><div class="story-thumb" role="img" aria-label="Hands preparing dough" style="background:linear-gradient(135deg,#e8dcd2,#c49074)"></div><div class="story-body"><div class="story-name">PORRO QUISQUAM</div><div class="stars"><i></i><i></i><i></i><i class="off"></i><i class="off"></i></div><div class="story-meta">200 Reviews , 10 Follower</div></div></div>
  <div class="story"><div class="story-thumb" role="img" aria-label="Pizza with greens" style="background:linear-gradient(135deg,#c9b79c,#8f9a5a)"></div><div class="story-body"><div class="story-name">ASIF BON VIVEUR</div><div class="stars"><i></i><i></i><i></i><i class="off"></i><i class="off"></i></div><div class="story-meta">200 Reviews , 10 Follower</div></div></div>
  <div class="view-more">View More »</div>
</aside>

<div class="abs partner" style="left:330px;width:170px;background:#e9e9e9;border-radius:30px"></div>
<div class="abs partner" style="left:552px;width:166px;background:#f4d3d2;border-radius:4px"></div>
<div class="abs partner" style="left:780px;width:92px;background:#e9e1dc;border-radius:50%"></div>

<footer class="abs site-footer">
  <div class="abs footer-links"><span>ABOUT</span>|<span>PRIVACY</span>|<span>TERMS</span>|<span>LEGAL</span>|<span>CONTACT</span></div>
  <div class="abs footer-social"><i></i><i></i><i></i><i></i><i></i><i></i></div>
  <div class="abs copyright">Copyright © 2017&nbsp; All Rights Reserved</div>
</footer>

</body>
</html>
```